Venture Capital firm needs modern business cards

We are a Venture Capital firm within financial services/Asset management. The industry generally has basic business cards with black, blue and maybe green/yellow design elements.
Our firm has a four-colour swoosh logo. We are based in London and want to stand out, just a little bit!, from the crowd. Our company is called LORV Investments and the 'C' stands for collaboration thus using makerswarm is a natural portal for our business card design competition. Our logo came via makerswarm too!
We use 'Venture Partner in Asset Management' as our tagline and this is Trademark registered. We operate in a conservative industry and we should not overstep our mark. The logo is colorful as it is and therefore the rest of the design should not be too fanciful.
The objective is twofold: make our logo element stick and memorable with our audience, whilst representing a conservative yet young image.
Updates
The Business Card obviously needs a field for Name, Surname, Job Title, Adress fields: Street, City, Postcode, Country, telefone and cell number, website address, etc.
We have uploaded the ai file. We trust that these are OK. If not, please advise.
Reason: We have have been busy with a client engagement. We will set the project as Guaranteed in return for the troubles we cause. Apologies for the confusion.
Thank you all for these great and creative design suggestions. The team is very happy with a number of your ideas! We will be in touch tomorrow to give individual feedback before the project closes on Friday. We look forward to working with some of you to narrow down your creations. Thank you, LORV Investments team.
All,
Target Market(s)
Financial Services Professionals, Investors, Media, 35-70 years, mainly male, well educated
Industry/Entity Type
Conservative
Requirements
Must have
- We must make use of our logo and potential tagline 'Venture Partner in Asset Management' as we are establishing a new Brand and new company in the market.
We can use 'LORV', 'LORV Investments', and 'LORV Investments'+tagline 'Venture Partner in Asset Management' or simply the four-colour swoosh plus the name of the company as part of the text. (see files)
All design elements are available in black or grey-scale if required. (grey scale swoosh attached).
Due to regulation we must have the following wording on the card in small print 'LORV Investments is an Appointed Representative of Bramwell Holdings Partnership Limited, which is authorised by the Monetary Oversight Board'.
Nice to have
- We would consider designs that make use of different printing techniques such embossing/debossing, UV spot etc.
We attach our colour palette in the files section for your reference.
Should not have
- The font we use for our company name is 'EXO' so do not use a font style that clashes with the corporate fonts, please.
Do not use other design elements than the ones we provide in the file library as part of this project.

```html
<!DOCTYPE html>
<html lang="en">
<head>
<meta charset="utf-8">
<title>LORV Investments – Business Card</title>
<link href="https://fonts.googleapis.com/css2?family=Fira+Sans:wght@300;400;500&display=swap" rel="stylesheet">
<style>
  :root {
    --canvas: #e9e8e6;
    --card-dark: #3a3a3a;
    --card-light: #ececec;
    --ink: #3c3c3c;
    --ink-soft: #5a5a5a;
    --on-dark: #e6e6e6;
    --accent-orange: #f0a019;
    --shadow: rgba(0,0,0,0.18);
  }
  * { margin: 0; padding: 0; box-sizing: border-box; }
  html, body {
    width: 1200px; height: 900px; overflow: hidden;
    background: var(--canvas);
    font-family: "Fira Sans", sans-serif;
  }
  .canvas {
    width: 1200px; height: 900px;
    display: flex; flex-direction: column;
    align-items: center; justify-content: center; gap: 56px;
  }
  .card {
    width: 630px; height: 360px; position: relative;
    border-radius: 3px;
    box-shadow: 0 6px 18px var(--shadow);
    overflow: hidden;
  }

  /* Front */
  .card--front { background: var(--card-dark); color: var(--on-dark); }
  .front-wordmark {
    position: absolute; right: 48px; top: 44px;
    text-align: right;
  }
  .front-wordmark__name {
    font-size: 96px; font-weight: 400; letter-spacing: 2px; line-height: 1;
    display: flex; align-items: center; gap: 18px;
  }
  .front-wordmark__dot {
    width: 22px; height: 22px; border-radius: 50%;
    background: var(--accent-orange);
  }
  .front-wordmark__sub {
    font-size: 22px; font-weight: 300; letter-spacing: 7px; margin-top: 6px;
  }

  /* Back */
  .card--back { background: var(--card-light); color: var(--ink); }
  .back-wordmark {
    position: absolute; left: 200px; top: 46px;
    display: flex; align-items: center; gap: 14px;
    font-size: 58px; font-weight: 400; letter-spacing: 1px; line-height: 1;
  }
  .back-wordmark__dot {
    width: 16px; height: 16px; border-radius: 50%;
    background: var(--accent-orange);
  }
  .address {
    position: absolute; right: 40px; top: 132px;
    text-align: right; font-size: 13px; line-height: 1.5; color: var(--ink-soft);
  }
  .person { position: absolute; left: 40px; top: 188px; }
  .person__name { font-size: 21px; font-weight: 400; }
  .person__title { font-size: 15px; font-weight: 300; margin-top: 2px; }
  .contacts {
    margin-top: 18px; font-size: 15px; font-weight: 300; line-height: 1.35;
    display: grid; grid-template-columns: 22px auto;
  }
  .legal {
    position: absolute; left: 40px; right: 40px; bottom: 22px;
    font-size: 9.5px; color: var(--ink-soft); line-height: 1.4;
  }
</style>
</head>
<body>
<main class="canvas">
  <section class="card card--front" aria-label="Card front">
    <div class="front-wordmark">
      <div class="front-wordmark__name"><span class="front-wordmark__dot"></span>LORV</div>
      <div class="front-wordmark__sub">Investments</div>
    </div>
  </section>

  <section class="card card--back" aria-label="Card back">
    <div class="back-wordmark"><span class="back-wordmark__dot"></span>LORV</div>
    <address class="address" style="font-style:normal">
      Harrow Lane 14, Kenton<br>
      London HA3 9QT, UK.<br>
      www.lorvinvest.com
    </address>
    <div class="person">
      <div class="person__name">Oliver James Hartley</div>
      <div class="person__title">Founder &amp; CEO</div>
      <div class="contacts">
        <span>T</span><span>207 555 0148</span>
        <span>M</span><span>207 555 0148</span>
        <span>E</span><span>oliver@lorvinvest.com</span>
      </div>
    </div>
    <p class="legal">LORV Investments is an Appointed Representative of Bramwell Holdings Partnership Limited,<br>which is authorised by the Monetary Oversight Board</p>
  </section>
</main>
</body>
</html>
```